Building company buisness cards

We are looking for a sharp modern new look for our business cards.
We are a New Zealand based company that specialises in house and land packages.
We have attached a photo of the current logo and would like to see if it can be improved somehow if needed.
We are open to any colours but we have chosen green at this stage.
Feel free to change the font and make the logo smarter looking.
Play with the colours and see what looks best.

We want a card that looks so good know one will want to throw it away!

Target Market(s)

Home buyers

Industry/Entity Type

Building

Contact Information for Business Card

Derek Tolvane
0217394062
dtolvane@quillmarkhomesteads.co.nz
quillmarkhomesteads.co.nz

Font styles to use
Serif
Sans Serif

Colors

Designer to choose colors to be used in the design.

Requirements
Must have
• Logo and company name on one side, details on the other side
Nice to have
• Color codes for the original green are HEX #4a8028, RGB(74,128,40), CMYK(42,0,69,50)
• Round corners, Raised and/or spot UV

```html
<!DOCTYPE html>
<html lang="en">
<head>
<meta charset="utf-8">
<title>Quillmark Homesteads – Business Card</title>
<link rel="stylesheet" href="https://fonts.googleapis.com/css2?family=Open+Sans:wght@300;400&display=swap">
<style>
  :root {
    --backdrop: #2a2a2a;
    --card-white: #f4f4f4;
    --brand-green: #0f8a1f;
    --swoosh-black: #111111;
    --ink-dark: #0c0c0c;
    --ink-light: #ffffff;
  }
  * { margin: 0; padding: 0; box-sizing: border-box; }
  html, body {
    width: 1200px;
    height: 923px;
    overflow: hidden;
    background: var(--backdrop);
    font-family: "Open Sans", Arial, sans-serif;
  }
  .canvas {
    position: relative;
    width: 1200px;
    height: 923px;
    display: flex;
    align-items: center;
    justify-content: center;
  }
  .business-card {
    position: relative;
    width: 900px;
    height: 514px;
    background: var(--card-white);
    border-radius: 6px;
    overflow: hidden;
    box-shadow: 0 18px 40px rgba(0,0,0,0.45);
  }
  .card-shapes {
    position: absolute;
    inset: 0;
    width: 100%;
    height: 100%;
  }
  .brand-block {
    position: absolute;
    left: 50px;
    top: 205px;
    width: 340px;
    display: flex;
    align-items: center;
    justify-content: center;
    gap: 14px;
  }
  .brand-mark {
    width: 44px;
    height: 44px;
    flex: none;
    background: var(--brand-green);
  }
  .brand-name {
    font-weight: 400;
    font-size: 28px;
    line-height: 1.15;
    color: var(--brand-green);
  }
  .holder-name {
    position: absolute;
    right: 40px;
    top: 62px;
    font-size: 24px;
    font-weight: 400;
    color: var(--ink-dark);
  }
  .contact-list {
    position: absolute;
    right: 40px;
    top: 282px;
    list-style: none;
    text-align: right;
    color: var(--ink-light);
    font-size: 17px;
    font-weight: 300;
    line-height: 27px;
  }
  .contact-item {
    display: flex;
    justify-content: flex-end;
    align-items: center;
    gap: 8px;
  }
  .contact-icon {
    width: 15px;
    height: 15px;
    flex: none;
  }
</style>
</head>
<body>
<main class="canvas">
  <article class="business-card">
    <svg class="card-shapes" viewBox="0 0 900 514" aria-hidden="true">
      <path d="M440 0 C350 150 420 360 540 514 L900 514 L900 0 Z" fill="var(--brand-green)"/>
      <path d="M426 0 C336 150 406 360 526 514" fill="none" stroke="var(--swoosh-black)" stroke-width="7"/>
      <path d="M415 0 C325 150 395 360 515 514" fill="none" stroke="var(--swoosh-black)" stroke-width="1.5"/>
    </svg>

    <div class="brand-block">
      <span class="brand-mark" role="img" aria-label="Company mark"></span>
      <p class="brand-name">Quillmark<br>Homesteads</p>
    </div>

    <h1 class="holder-name">Derek Tolvane</h1>

    <ul class="contact-list">
      <li class="contact-item">
        <span>0217394062</span>
        <svg class="contact-icon" viewBox="0 0 16 16" aria-label="phone">
          <rect width="16" height="16" rx="2" fill="var(--ink-dark)"/>
          <path d="M5 3.5 L6.8 5.6 L5.9 6.8 C6.6 8.2 7.8 9.4 9.2 10.1 L10.4 9.2 L12.5 11 L11.4 12.5 C7.6 12.2 3.8 8.4 3.5 4.6 Z" fill="var(--ink-light)"/>
        </svg>
      </li>
      <li class="contact-item">
        <span>dtolvane@quillmarkhomesteads.co.nz</span>
        <svg class="contact-icon" viewBox="0 0 16 16" aria-label="email">
          <rect width="16" height="16" rx="2" fill="var(--ink-dark)"/>
          <rect x="3" y="4.5" width="10" height="7" fill="none" stroke="var(--ink-light)" stroke-width="1.2"/>
          <path d="M3 4.5 L8 8.5 L13 4.5" fill="none" stroke="var(--ink-light)" stroke-width="1.2"/>
        </svg>
      </li>
      <li class="contact-item">
        <span>quillmarkhomesteads.co.nz</span>
        <svg class="contact-icon" viewBox="0 0 16 16" aria-label="website">
          <rect width="16" height="16" rx="2" fill="var(--ink-dark)"/>
          <circle cx="8" cy="8" r="4.8" fill="none" stroke="var(--ink-light)" stroke-width="1.1"/>
          <ellipse cx="8" cy="8" rx="2" ry="4.8" fill="none" stroke="var(--ink-light)" stroke-width="1"/>
          <line x1="3.2" y1="8" x2="12.8" y2="8" stroke="var(--ink-light)" stroke-width="1"/>
        </svg>
      </li>
    </ul>
  </article>
</main>
</body>
</html>
```